Business Card Update, need to bring life to the card, two sided color

We need a new business card design, are moving and changing addresses and need a new look, we have the logos already attached but need a new style moving forward. Can incorporate the color of the logo (The Green) as well, maybe a solid back? We deal with safety products revolving around static electricity and safety lighting. Would like to keep same font in second logo as well.

Target Market(s)

Electrical Safety, Lighting

Contact Information for Business Card

Dale Fenwick
Vice President
Office: 770-555-4821
Cell: 770-555-3067
dale@tkfenwick.example
www.tkfenwick.example
4700 West Harbor Boulevard
Suite #150
Roswell, GA 30076

Font styles to use
Serif
Sans Serif

Requirements
Must have
• Since 1918
Nice to have
• Could use the 100 Year Logo for back of card, would like the back of card to be the same green as logo.
Should not have
• No black cards please.

```html
<!DOCTYPE html>
<html lang="en">
<head>
<meta charset="utf-8">
<title>T.K. Fenwick Business Card</title>
<link rel="stylesheet" href="https://fonts.googleapis.com/css2?family=Lato:wght@400;700;900&display=swap">
<style>
  :root {
    --brand-green: #0f9b5a;
    --ink: #1d1d1d;
    --paper: #ffffff;
    --divider: #d6d6d6;
    --backdrop: #8e8e8e;
  }
  * { box-sizing: border-box; margin: 0; padding: 0; }
  html, body { width: 1200px; height: 782px; overflow: hidden; }
  body {
    background: var(--backdrop);
    font-family: "Lato", Arial, sans-serif;
    position: relative;
  }
  .card {
    position: absolute;
    top: 240px;
    width: 520px;
    height: 298px;
    box-shadow: 0 6px 16px rgba(0,0,0,0.3);
    overflow: hidden;
  }
  .card-front { left: 50px; background: var(--paper); }
  .card-back  { left: 630px; background: var(--brand-green); }

  .front-band {
    position: absolute; left: 0; right: 0; bottom: 0;
    height: 12px; background: var(--brand-green);
  }
  .brand-block {
    position: absolute; left: 22px; top: 62px; width: 220px;
    text-align: center; color: var(--brand-green);
  }
  .brand-mark {
    width: 70px; height: 70px; border-radius: 50%;
    border: 4px solid var(--brand-green);
    margin: 0 auto 10px;
  }
  .brand-name {
    font-weight: 900; font-size: 27px; line-height: 1.05; white-space: nowrap;
  }
  .brand-sub {
    font-weight: 900; font-size: 13.5px; margin-top: 3px; white-space: nowrap;
  }
  .brand-since {
    font-weight: 700; font-size: 12px; margin-top: 6px; letter-spacing: 1px;
    text-transform: uppercase; white-space: nowrap;
  }
  .front-divider {
    position: absolute; left: 262px; top: 50px; width: 2px; height: 190px;
    background: var(--divider);
  }
  .contact-block {
    position: absolute; left: 282px; top: 52px; width: 226px; color: var(--ink);
  }
  .contact-name {
    color: var(--brand-green); font-weight: 700; font-size: 21px; line-height: 1;
  }
  .contact-title { font-size: 14px; margin: 3px 0 6px; }
  .contact-list { list-style: none; }
  .contact-list li {
    display: flex; align-items: center; gap: 6px;
    font-size: 15px; line-height: 19px; white-space: nowrap;
  }
  .contact-list svg { width: 11px; height: 11px; flex: none; }
  .contact-address { font-size: 15px; line-height: 19px; margin-top: 2px; white-space: nowrap; }

  .back-pattern {
    position: absolute; inset: 0;
    background: radial-gradient(circle at 50% 50%, #16a563 0%, var(--brand-green) 70%);
  }
  .back-mark {
    position: absolute; left: 50%; top: 50%;
    transform: translate(-50%, -50%);
    display: flex; flex-direction: column; align-items: center; gap: 8px;
    color: var(--paper);
  }
  .back-mark-circle {
    width: 46px; height: 46px; border-radius: 50%; background: var(--paper);
  }
  .back-mark-name { font-weight: 900; font-size: 18px; white-space: nowrap; }
</style>
</head>
<body>
  <section class="card card-front" aria-label="Business card front">
    <div class="brand-block">
      <div class="brand-mark"></div>
      <div class="brand-name">T.K. Fenwick</div>
      <div class="brand-sub">Manufacturing Company, Inc.</div>
      <div class="brand-since">Since 1918</div>
    </div>
    <div class="front-divider"></div>
    <div class="contact-block">
      <div class="contact-name">Dale Fenwick</div>
      <div class="contact-title">Vice President</div>
      <ul class="contact-list">
        <li>
          <svg viewBox="0 0 12 12" aria-hidden="true"><path fill="#0f9b5a" d="M2 1h2l1 3-1.5 1a7 7 0 0 0 3.5 3.5L8 7l3 1v2a1 1 0 0 1-1 1A9 9 0 0 1 1 2a1 1 0 0 1 1-1z"/></svg>
          770-555-4821
        </li>
        <li>
          <svg viewBox="0 0 12 12" aria-hidden="true"><rect x="2.5" y="0.5" width="7" height="11" rx="1" fill="none" stroke="#0f9b5a" stroke-width="1.4"/></svg>
          770-555-3067
        </li>
        <li>
          <svg viewBox="0 0 12 12" aria-hidden="true"><rect x="0.5" y="2" width="11" height="8" rx="1" fill="#0f9b5a"/><path d="M1 3l5 4 5-4" fill="none" stroke="#fff" stroke-width="1"/></svg>
          dale@tkfenwick.example
        </li>
        <li>
          <svg viewBox="0 0 12 12" aria-hidden="true"><circle cx="6" cy="6" r="5.5" fill="#0f9b5a"/><path d="M0.5 6h11M6 0.5c-2.5 3-2.5 8 0 11M6 0.5c2.5 3 2.5 8 0 11" fill="none" stroke="#fff" stroke-width="0.8"/></svg>
          www.tkfenwick.example
        </li>
      </ul>
      <p class="contact-address">4700 West Harbor Boulevard<br>Suite #150<br>Roswell, GA 30076</p>
    </div>
    <div class="front-band"></div>
  </section>

  <section class="card card-back" aria-label="Business card back">
    <div class="back-pattern" role="img" aria-label="Repeating pattern of faint brand emblems on green"></div>
    <div class="back-mark">
      <div class="back-mark-circle"></div>
      <div class="back-mark-name">T.K. Fenwick</div>
    </div>
  </section>
</body>
</html>
```